Resposive web site in 4 languages + image gallery + logo design

We need a web page, which will work on all devices.
I have uploaded web page concept.
Company name: Praxelun
Industry/Entity Type
It Company
Logo Text
quality matters
Coding
Coded - Design and coding required
Number of Pages Required
1 page

```html
<!DOCTYPE html>
<html lang="en">
<head>
<meta charset="utf-8">
<title>Praxelun — Woodworks, Stoneworks, Restoration</title>
<link rel="stylesheet" href="https://fonts.googleapis.com/css2?family=Oswald:wght@400;500&family=Roboto:wght@400;500;700&display=swap">
<style>
:root{
  --accent:#c2561c;
  --link:#2a67b1;
  --ink:#222;
  --text:#555;
  --band:#f1f1f1;
  --line:#cfcfcf;
  --about-dark:#5e4030;
  --about-light:#8a6650;
  --footer:#1f1f1f;
  --white:#fff;
}
*{box-sizing:border-box;margin:0;padding:0}
html,body{width:1200px;height:2853px;overflow:hidden}
body{font-family:"Roboto",Arial,sans-serif;color:var(--text);background:var(--white);position:relative}
section,header,footer{position:relative;width:1200px}
.abs{position:absolute}

/* header */
.site-header{height:105px;background:var(--white)}
.brand{left:87px;top:30px;font-family:"Oswald",sans-serif;font-weight:500;font-size:40px;color:var(--accent);letter-spacing:.5px}
.main-nav{left:624px;top:49px;display:flex;gap:0;font-size:16px;color:#333}
.main-nav span{margin-right:44px}
.lang-select{left:983px;top:44px;width:90px;height:32px;border:1px solid #777;font-size:12px;color:#333;display:flex;align-items:center;justify-content:center;gap:6px}
.social-square{left:1092px;top:50px;width:20px;height:20px;background:#3b66b0;border-radius:3px}

/* hero */
.hero{height:591px}
.hero-photo{inset:0;background:linear-gradient(135deg,#4a3b31 0%,#7c6957 35%,#a8957f 60%,#5d4c3e 100%)}
.hero-shade{inset:0;background:rgba(0,0,0,.18)}
.hero-title{left:0;right:0;top:250px;text-align:center;font-family:"Oswald",sans-serif;font-size:42px;color:var(--white);letter-spacing:.5px}
.hero-btn{left:510px;top:327px;width:180px;height:51px;border:1px solid var(--white);color:var(--white);font-size:20px;display:flex;align-items:center;justify-content:center}
.dots{left:548px;top:538px;display:flex;gap:9px}
.dots i{width:14px;height:14px;border-radius:50%;background:var(--white);display:block}
.dots i.on{background:var(--accent)}

/* services */
.services-head{height:150px}
.section-title{left:0;right:0;top:58px;text-align:center;font-family:"Oswald",sans-serif;font-size:30px;color:var(--ink)}
.section-title em,.accent{font-style:normal;color:var(--accent)}
.service{height:370px}
.service.alt{background:var(--band)}
.service-photo{width:425px;height:266px;border:4px solid var(--white);outline:1px solid var(--line)}
.service-name{font-family:"Oswald",sans-serif;font-size:23px;color:var(--accent)}
.service-text{width:576px;font-size:14px;line-height:23px;color:var(--text)}
.service-text p+p{margin-top:14px}
.tags{display:grid;gap:14px 0;font-size:13px;font-weight:700;color:var(--link)}
.tags span::before{content:"\00BB";margin-right:7px}

/* about */
.about{height:360px;background:linear-gradient(90deg,var(--about-light),var(--about-dark) 60%,#74533f)}
.about-title{left:90px;top:62px;font-family:"Oswald",sans-serif;font-size:24px;color:var(--white)}
.about-text{left:90px;top:104px;width:575px;font-size:14px;line-height:23px;color:var(--white)}
.about-sign{left:90px;top:260px;font-size:15px;line-height:23px;color:var(--white)}
.about-photo{left:689px;top:61px;width:422px;height:263px;border:4px solid var(--white);background:linear-gradient(135deg,#3a2a20,#8a6a4c 50%,#2c2019)}

/* contact */
.contact{height:451px}
.label{font-family:"Oswald",sans-serif;font-size:18px;color:var(--accent)}
.info-row{left:93px;display:flex;align-items:center;gap:14px;font-size:15px;color:#444}
.map{left:91px;top:218px;width:535px;height:191px;background:linear-gradient(135deg,#dedede,#cbcbcb)}
.form-title{left:664px;top:44px;font-family:"Oswald",sans-serif;font-size:25px;color:var(--ink)}
.form-note{left:664px;top:84px;font-size:11px;font-weight:500;color:#333}
.field{left:664px;width:443px;border:1px solid #bbb;font-size:13px;color:#333;padding:14px 12px}
.send{left:664px;top:369px;width:116px;height:38px;background:var(--accent);color:var(--white);font-size:15px;display:flex;align-items:center;justify-content:center}

/* footer */
.site-footer{height:104px;background:var(--footer)}
.copyright{left:89px;top:45px;font-size:12px;color:#ddd}
.footer-social{left:980px;top:34px;display:flex;gap:17px}
.footer-social i{display:block;width:34px;height:34px;border:1px solid #ccc;border-radius:50%}
</style>
</head>
<body>

<header class="site-header">
  <div class="abs brand">PRAXELUN</div>
  <nav class="abs main-nav"><span>SERVICES</span><span>ABOUT US</span><span>CONTACT</span></nav>
  <div class="abs lang-select">ENGLISH
    <svg width="8" height="6" viewBox="0 0 8 6"><path d="M1 1l3 3 3-3" stroke="#333" fill="none" stroke-width="1.3"/></svg>
  </div>
  <div class="abs social-square"></div>
</header>

<section class="hero">
  <div class="abs hero-photo" role="img" aria-label="Craftsman in safety glasses working on a piece of timber"></div>
  <div class="abs hero-shade"></div>
  <h1 class="abs hero-title">ARE YOU INTERESTED IN AN ESTIMATE?</h1>
  <div class="abs hero-btn">GET A QUOTE</div>
  <div class="abs dots"><i class="on"></i><i></i><i></i><i></i><i></i></div>
</section>

<section class="services-head">
  <h2 class="abs section-title">OUR <em>SERVICES</em></h2>
</section>

<section class="service">
  <div class="abs service-photo" style="left:87px;top:12px;background:linear-gradient(135deg,#cfc3b5,#9b7f62 50%,#e2dbd3)" role="img" aria-label="Carpenter cutting planks in a woodworking shop"></div>
  <h3 class="abs service-name" style="left:538px;top:16px">WOODWORKS</h3>
  <div class="abs service-text" style="left:538px;top:54px">
    <p>Timber is, in essence, a natural and warm material. Wood is also relatively durable and easy to work with, which has made it a favourite of builders throughout history. Our goal is to offer GALLERY (sliders) suitable products and quality furniture with installation and after-When cliked opens sales service to all of our clients. In order to achieve this, we're this category gallery ready to help our clients in all stages of construction from design to production and maintenance.</p>
  </div>
  <div class="abs tags" style="left:538px;top:206px;grid-template-columns:140px 152px 120px">
    <span>FURNITURE</span><span>WINDOWS</span><span>DOORS</span>
    <span>STAIRCASES</span><span>WOODCARVING</span><span>GRAINING</span>
  </div>
</section>

<section class="service alt" style="height:360px">
  <div class="abs service-photo" style="left:86px;top:46px;background:linear-gradient(180deg,#8fae6a,#b9b6ae 45%,#9e9c96)" role="img" aria-label="Stone path being laid through a garden"></div>
  <h3 class="abs service-name" style="left:536px;top:50px">STONEWORKS</h3>
  <div class="abs service-text" style="left:536px;top:89px">
    <p>The natural stone found in the ground has been used in construction for centuries because of its durability. A structure GALLERY (sliders) built by a skilled craftsman from natural stone is unique, genuine When cliked opens and durable, and perfect for our bracing climate.</p>
    <p>Our experienced craftsmen are ready to help you in all stages of construction from planning to completion.</p>
  </div>
  <div class="abs tags" style="left:536px;top:246px;grid-template-columns:184px 137px 118px 100px">
    <span>WALLS</span><span>TERRACES</span><span>PATHS</span><span>FENCES</span>
    <span style="grid-column:span 1">OUTDOOR KITCHENS</span><span>FIREPLACES</span><span>SMOKERIES</span>
  </div>
</section>

<section class="service" style="height:403px">
  <div class="abs service-photo" style="left:91px;top:42px;background:linear-gradient(135deg,#3e2a1c,#9a6332 45%,#d8d3ca)" role="img" aria-label="Restored wooden extending table in a showroom"></div>
  <h3 class="abs service-name" style="left:542px;top:44px">RESTORATION</h3>
  <div class="abs service-text" style="left:542px;top:82px">
    <p>It's good to see that fixing old things has become popular again in recent years and people are trying to find ways to preserve GALLERY (sliders) valuable old windows and pieces of furniture before deciding to When cliked opens replace them.</p>
    <p>It is possible to give a new life to almost any wooden door, window, piece of furniture or staircase. The extensive experience of our craftsmen will help you achieve the desired result.</p>
  </div>
  <div class="abs tags" style="left:542px;top:244px;grid-template-columns:138px 138px 120px">
    <span>FURNITURE</span><span>WINDOWS</span><span>DOORS</span>
    <span>STAIRCASES</span><span>FLOORS</span><span>SPECIAL PROJECTS</span>
  </div>
</section>

<section class="about">
  <h2 class="abs about-title">ABOUT US</h2>
  <div class="abs about-text">Praxelun is a company whose business operations include making wooden products, restoration and building structures from natural stone. LOGO OR IMAGE All of our products are made by craftsmen and specialists who have extensive experience and knowledge in their fields.<br>The products we offer are always handmade and we take the requests and ideas of the specific client into account We always strive to achieve the best possible quality.</div>
  <div class="abs about-sign">Quality matters,<br>Praxelun</div>
  <div class="abs about-photo" role="img" aria-label="Woodworking tools and wooden offcuts on a workbench"></div>
</section>

<section class="contact">
  <h3 class="abs label" style="left:93px;top:70px">ADDRESS</h3>
  <div class="abs info-row" style="top:112px">
    <svg width="12" height="16" viewBox="0 0 12 16"><path d="M6 0a6 6 0 0 0-6 6c0 4.5 6 10 6 10s6-5.5 6-10a6 6 0 0 0-6-6zm0 8.5A2.5 2.5 0 1 1 6 3.5a2.5 2.5 0 0 1 0 5z" fill="var(--accent)"/></svg>
    <span>Korva 12 &nbsp;10115 Tallinn &nbsp;ESTONIA</span>
  </div>
  <div class="abs info-row" style="top:142px;font-size:19px">
    <svg width="14" height="14" viewBox="0 0 14 14"><rect width="14" height="14" rx="2" fill="var(--accent)"/><path d="M4 3.5l1.6 0 .7 2-1 .8a5 5 0 0 0 2.4 2.4l.8-1 2 .7v1.6c-3.8.6-7-2.6-6.5-6.5z" fill="#fff"/></svg>
    <span>+372 55 01234</span>
  </div>
  <div class="abs info-row" style="top:178px">
    <svg width="14" height="11" viewBox="0 0 14 11"><rect width="14" height="11" rx="1" fill="var(--accent)"/><path d="M1 1.5l6 4.5 6-4.5" stroke="#fff" fill="none" stroke-width="1.3"/></svg>
    <span>hello@praxelun.ee</span>
  </div>
  <div class="abs map" role="img" aria-label="Street map of the workshop location with a pin"></div>

  <h2 class="abs form-title">CONTACT US <span class="accent">FORM</span></h2>
  <div class="abs form-note">PLEASE FILL IN THE FOLLOWING FIELDS IF YOU WOULD LIKE A PRICE QUOTE</div>
  <div class="abs field" style="top:114px;height:47px">Name</div>
  <div class="abs field" style="top:169px;height:47px">Email</div>
  <div class="abs field" style="top:224px;height:50px">Phone</div>
  <div class="abs field" style="top:281px;height:80px">Message</div>
  <div class="abs send">SEND</div>
</section>

<footer class="site-footer">
  <div class="abs copyright">Copyright © 2016. All Rights Reserved</div>
  <div class="abs footer-social"><i></i><i></i><i></i></div>
</footer>

</body>
</html>
```